Harborline Business Card Designs***

WE ARE A FULL SERVICE FACILITY. ALL KINDS OF CAR/ TRK, REPAIR. CUSTOM WHEELS & TIRES. BRAKES, MUFFLERS, SHOCK, STRUTS...BATTERIES, STARTERS, ATERNATORS, TUNE UPS (WE DO IT ALL) ESTABLISHED IN 2004, LOCALLY OWNED AND OPERATED.... I AM OPEN TO SUGGESTIONS AS WELL ON ANY IDEAS

Contact Information for Business Card

WE DO COMPLETE AUTO REPAIR AND WHEELS, TIRES AND ACCESSORIES AT OUR STORE. I NAME OF SHOP (HARBORLINE AUTOMOTIVE GROUP) WOULD LIKE OUR EMAIL ON IT (HARBORLINEAUTOGROUP@QUVIX.NET) PHONE NUMBER 567-302-GEAR (4327) BUSINESS HOURS MON- FRI 7:30-5 SNAPGRID LOGO WITH (@HARBORLINE_AUTO_WESTRIDGE) WEBSITE (KESTRELROADWORKS.NET)FRIENDLOOP LOGO W/ (FRIENDLOOP.NET/HARBORLINEAUTOMOTIVE) AN A+/ QCR LOGO (THE LITTLE TORCH)... MAYBE EVEN EST.2004 INSIDE OF A "POW SIGN" (UNLESS IT GETS TO CLUTTERED) AND ON THE BACK OF THE CARD MAYBE A FAINT PICTURE OF "SOMETHING" IN BACKGROUND BUT STILL BE ABLE TO SEE THE ESTIMATE WE WRITE ON THE BACK. I WOULD LIKE ON THE BACK, DOWN IN THE RIGHT HAND CORNER A SPOT FOR A DATE AND INT. WE ALSO EXCEPT: ORBA, TRUSTPLATE, KELMORE AND ZINCWAY

```html
<!DOCTYPE html>
<html lang="en">
<head>
<meta charset="utf-8">
<title>Harborline Automotive Group – Business Card</title>
<link href="https://fonts.googleapis.com/css2?family=Roboto+Condensed:wght@400;700&display=swap" rel="stylesheet">
<style>
  :root {
    --stage: #050608;
    --card-base: #e6e7ea;
    --brand-blue: #1a8fd6;
    --hours-blue: #2b3990;
    --ink: #161616;
    --muted: #b9bcc2;
    --burst: #17a9e6;
    --rule-dark: #2a2a2a;
  }
  * { box-sizing: border-box; margin: 0; padding: 0; }
  html, body { width: 1200px; height: 1200px; overflow: hidden; background: var(--stage); }
  body { position: relative; font-family: "Roboto Condensed", sans-serif; color: var(--ink); }

  .card { position: absolute; left: 231px; width: 738px; height: 443px; overflow: hidden; background: var(--card-base); }
  .card--front { top: 107px; }
  .card--back { top: 650px; }

  .card__photo { position: absolute; inset: 0; }
  .card--front .card__photo {
    background: radial-gradient(ellipse at 55% 35%, #f1f1f3 0%, #d9dade 45%, #cfd0d5 100%);
  }
  .card--back .card__photo {
    background: linear-gradient(180deg, #f4f4f5 0%, #dcdde0 45%, #e2e3e6 100%);
  }
  .back__band { position: absolute; left: 0; right: 0; top: 184px; height: 134px; background: rgba(255,255,255,0.55); }

  .wordmark { position: absolute; left: 0; right: 0; text-align: center; }
  .wordmark__name { font-weight: 700; color: var(--brand-blue); letter-spacing: 3px; line-height: 1; }
  .wordmark__sub { font-weight: 400; letter-spacing: 5px; line-height: 1; color: var(--ink); }

  .card--front .wordmark { top: 92px; }
  .card--front .wordmark__name { font-size: 64px; }
  .card--front .wordmark__sub { font-size: 33px; margin-top: 6px; }
  .hours { position: absolute; left: 0; right: 0; top: 189px; text-align: center; font-size: 23px; color: var(--hours-blue); }

  .rule { position: absolute; left: 8px; right: 8px; height: 3px;
    background: linear-gradient(90deg, transparent 0%, #9a9a9a 12%, var(--rule-dark) 30%, #b0b0b0 50%, var(--rule-dark) 72%, #9a9a9a 88%, transparent 100%); }
  .card--front .rule { top: 240px; }
  .card--back .rule { top: 319px; }

  .contact-row { position: absolute; left: 0; right: 0; display: flex; justify-content: center; align-items: center; font-size: 16px; }
  .contact-row--one { top: 262px; height: 40px; }
  .contact-row--two { top: 314px; height: 40px; }
  .contact-row--three { top: 364px; height: 32px; font-size: 17px; }
  .contact { display: flex; align-items: center; gap: 7px; padding: 0 10px; height: 100%; }
  .contact + .contact { border-left: 1px solid #555; }
  .contact svg { flex: none; }
  .square { width: 26px; height: 26px; border-radius: 4px; flex: none; }
  .square--snap { background: #5a4a42; }
  .square--loop { background: #4a6aa8; }
  .rating-badge { width: 22px; height: 30px; border-radius: 3px; background: #3f7a95; }

  .card--back .wordmark { top: 196px; left: 137px; right: auto; width: 320px; }
  .card--back .wordmark__name { font-size: 44px; }
  .card--back .wordmark__sub { font-size: 24px; margin-top: 3px; letter-spacing: 3px; }
  .back__address { position: absolute; left: 137px; width: 320px; top: 264px; text-align: center; font-size: 17px; }

  .burst { position: absolute; left: 485px; top: 172px; }

  .payments { position: absolute; left: 85px; top: 346px; display: flex; gap: 14px; align-items: center; font-size: 15px; font-weight: 700; }
  .payment { display: flex; align-items: center; gap: 5px; }
  .payment .dot { width: 12px; height: 12px; background: #6b6f78; }

  .estimate { position: absolute; left: 521px; top: 342px; font-size: 16px; line-height: 21px; }
  .estimate__hint { color: var(--muted); }
</style>
</head>
<body>

<section class="card card--front">
  <div class="card__photo" role="img" aria-label="Faint photograph of a chrome engine bay"></div>
  <div class="wordmark">
    <div class="wordmark__name">HARBORLINE</div>
    <div class="wordmark__sub">AUTOMOTIVE GROUP</div>
  </div>
  <div class="hours">BUSINESS HOURS MON- FRI 7:30-5</div>
  <div class="rule"></div>

  <div class="contact-row contact-row--one">
    <div class="contact">
      <svg width="26" height="26" viewBox="0 0 24 24"><path d="M6.6 10.8a15 15 0 0 0 6.6 6.6l2.2-2.2a1 1 0 0 1 1-.25 11.4 11.4 0 0 0 3.6.57 1 1 0 0 1 1 1V20a1 1 0 0 1-1 1A17 17 0 0 1 3 4a1 1 0 0 1 1-1h3.5a1 1 0 0 1 1 1c0 1.25.2 2.45.57 3.57a1 1 0 0 1-.25 1z" fill="#111"/></svg>
      <span>567-302-Gear (4327)</span>
    </div>
    <div class="contact">
      <svg width="30" height="30" viewBox="0 0 30 30"><circle cx="15" cy="15" r="13" fill="#111"/><ellipse cx="15" cy="15" rx="6" ry="13" fill="none" stroke="#fff" stroke-width="1.2"/><line x1="2" y1="15" x2="28" y2="15" stroke="#fff" stroke-width="1.2"/></svg>
      <span>kestrelroadworks.net</span>
    </div>
    <div class="contact">
      <svg width="34" height="24" viewBox="0 0 34 24"><rect x="1" y="1" width="32" height="22" fill="#111"/><path d="M2 2l15 12L32 2" fill="none" stroke="#fff" stroke-width="2"/><path d="M2 22l11-10M32 22L21 12" stroke="#fff" stroke-width="1.5"/></svg>
      <span>harborlineautogroup@quvix.net</span>
    </div>
  </div>

  <div class="contact-row contact-row--two">
    <div class="contact">
      <span class="square square--snap"></span>
      <span>harborline_auto_westridge</span>
    </div>
    <div class="contact">
      <span class="square square--loop"></span>
      <span>@harborlineautowestridge.</span>
    </div>
    <div class="contact">
      <span class="rating-badge"></span>
    </div>
  </div>

  <div class="contact-row contact-row--three">
    <div class="contact">
      <svg width="20" height="30" viewBox="0 0 20 30"><path d="M10 1a9 9 0 0 0-9 9c0 7 9 19 9 19s9-12 9-19a9 9 0 0 0-9-9z" fill="#111"/><circle cx="10" cy="10" r="3.5" fill="#fff"/></svg>
      <span>4815 W. Lakeview Ave. Westridge, OH 43990</span>
    </div>
  </div>
</section>

<section class="card card--back">
  <div class="card__photo" role="img" aria-label="Faint photograph of a row of custom chrome wheels"></div>
  <div class="back__band"></div>
  <div class="wordmark">
    <div class="wordmark__name">HARBORLINE</div>
    <div class="wordmark__sub">AUTOMOTIVE GROUP</div>
  </div>
  <div class="back__address">4815 W. Lakeview Ave. Westridge, OH 43990</div>

  <svg class="burst" width="150" height="90" viewBox="0 0 150 90" aria-label="Established 2004">
    <polygon fill="var(--burst)" points="2,42 28,30 38,8 60,22 78,2 92,20 122,10 118,32 148,42 120,52 128,74 98,64 84,88 66,68 40,82 40,60 14,62 24,50"/>
    <text x="74" y="52" text-anchor="middle" font-family="Roboto Condensed, sans-serif" font-size="26" fill="#fff">EST.2004</text>
  </svg>

  <div class="rule"></div>

  <div class="payments">
    <div class="payment"><span class="dot"></span>Zincway</div>
    <div class="payment"><span class="dot"></span>TrustPlate</div>
    <div class="payment"><span class="dot"></span>Orba</div>
    <div class="payment"><span class="dot"></span>Kelmore</div>
  </div>

  <div class="estimate">
    <div>DATE : <span class="estimate__hint">DD/MM/YYYY</span></div>
    <div>INT :</div>
  </div>
</section>

</body>
</html>
```